WordPress webdesign with coding for our company BRISK The Answer

BRISK The Answer is a payrolling company such as Montaval Wages (one of our competitor https://www.montaval-wages.ch/fr/). We need to set up our website in both languages (Fr and Eng). Our logo is enclosed.
we would like something simple explaining what is payrolling in Graph and wording, who we are and a contact page. you can also take some example if needed from our mother company BRISK The Horizon (www.briskthehorizon.ch) or our sister company (www.briskyourstride.ch). we would like to keep the color panel of our logo (ref. Black = PANTONE P Process Black C
Pink = PANTONE P Process Magenta C
Grey = PANTONE 430 C) as the driver of the website.

```html
<!DOCTYPE html>
<html lang="en">
<head>
<meta charset="utf-8">
<title>BRISK The Answer — Your Trusted Payrolling Partner</title>
<link rel="stylesheet" href="https://fonts.googleapis.com/css2?family=Montserrat:wght@400;500;600;700;800&family=Open+Sans:wght@400;600;700&display=swap">
<style>
:root{
  --ink:#111111;
  --pink:#e6177f;
  --grey:#7c878e;
  --soft:#f3f3f3;
  --text:#444444;
  --white:#ffffff;
}
*{margin:0;padding:0;box-sizing:border-box}
html,body{width:1200px;height:4220px;overflow:hidden;background:var(--white)}
body{position:relative;font-family:"Open Sans",Arial,sans-serif;color:var(--text)}
.abs{position:absolute}
.heading{font-family:"Montserrat",Arial,sans-serif;font-weight:400;color:var(--ink);font-size:34px;letter-spacing:.5px}
.heading b{font-weight:800}
.center{left:0;width:1200px;text-align:center}
.dots{display:flex;gap:5px;justify-content:center}
.dots i{width:10px;height:10px;border-radius:50%;background:var(--pink);display:block}
.btn{display:inline-flex;align-items:center;gap:8px;font-family:"Montserrat",Arial,sans-serif;font-weight:700;font-size:14px;color:var(--ink);border:2px solid var(--ink);border-radius:26px;padding:0 24px;height:48px;background:var(--white)}
.btn.light{border-color:var(--white)}
.tick{width:22px;height:14px}
.topbar{top:0;left:0;width:1200px;height:41px;background:var(--ink)}
.topbar .pinkzone{position:absolute;right:0;top:0;width:316px;height:41px;background:var(--pink);clip-path:polygon(16px 0,100% 0,100% 100%,0 100%)}
.call{top:6px;left:596px;display:flex;align-items:center;gap:12px;color:var(--white);font-size:15px}
.call b{font-weight:700}
.round{width:30px;height:30px;border-radius:50%;background:var(--pink);display:flex;align-items:center;justify-content:center}
.social-top{top:7px;left:990px;display:flex;gap:6px}
.social-top span{width:28px;height:28px;border-radius:50%;background:var(--white);display:block}
.logo{font-family:"Montserrat",Arial,sans-serif;font-weight:800;color:var(--ink);letter-spacing:1px}
.logo small{display:block;font-weight:500;letter-spacing:7px}
.nav{top:78px;left:536px;display:flex;gap:44px;font-family:"Montserrat",Arial,sans-serif;font-size:15px;font-weight:500;color:var(--ink)}
.nav .active{color:var(--pink)}
.hero-photo{top:118px;left:0;width:1200px;height:700px;background:linear-gradient(110deg,#2c3d4a 0%,#5f7283 35%,#9aa9b3 60%,#6d7a84 100%)}
.hero-title{top:246px;left:602px;font-family:"Montserrat",Arial,sans-serif;font-weight:700;color:var(--white);font-size:47px;line-height:55px}
.hero-sub{top:360px;left:602px;color:var(--white);font-size:20px}
.hero-btn{top:408px;left:602px}
.hero-btn .btn{height:44px;font-size:14px;border:none}
.lead{font-size:15px;line-height:27.5px;color:var(--text)}
.panel{top:1206px;left:134px;width:932px;height:488px;background:var(--soft);border-radius:36px}
.service{top:1345px;width:240px;text-align:center}
.ring{width:104px;height:104px;border-radius:50%;border:8px solid #3a3a3a;margin:0 auto;position:relative;display:flex;align-items:center;justify-content:center}
.ring::after{content:"";position:absolute;top:-2px;right:0;width:20px;height:20px;border-radius:50%;background:var(--pink);border:3px solid var(--soft)}
.service h3{font-family:"Montserrat",Arial,sans-serif;font-weight:500;font-size:17px;color:var(--ink);margin-top:18px}
.service p{font-size:13.5px;line-height:22px;margin-top:8px}
.divider{width:1px;height:197px;background:#cfcfcf;top:1355px}
.laptop-photo{top:1796px;left:93px;width:494px;height:282px;border-radius:10px;background:linear-gradient(180deg,#e9e9ec 0%,#d6d7db 70%,#4a4a4a 100%)}
.list li{list-style:none;display:flex;align-items:center;gap:14px;font-size:16px;color:var(--ink);height:38.5px}
.band{top:2179px;left:0;width:1200px;height:571px;background:var(--pink)}
.band-text{color:var(--white);font-size:15px;line-height:26px;width:450px;left:113px}
.band-photo{top:2290px;left:664px;width:370px;height:370px;border-radius:50%;background:radial-gradient(circle at 45% 45%,#3d6fa3 0%,#24384f 50%,#12161c 100%)}
.testi-bg{top:3186px;left:0;width:1200px;height:560px;background:var(--soft)}
.card{top:3366px;width:360px;height:194px;background:var(--white);border-radius:14px;padding:34px 24px 0 98px}
.stars{color:#f5b400;font-size:17px;letter-spacing:3px}
.card p{font-size:14.5px;line-height:24px;margin-top:8px;color:#555}
.card .who{font-size:13px;margin-top:10px;color:#777}
.card .who b{color:var(--ink);font-family:"Montserrat",Arial,sans-serif;font-weight:700;margin-right:8px}
.avatar{width:140px;height:140px;border-radius:50%;background:linear-gradient(160deg,#6d7a87,#2b3138);border:4px solid var(--white);top:3392px}
.foot{color:var(--white)}
.foot h4{font-family:"Montserrat",Arial,sans-serif;font-weight:700;font-size:18px}
.foot h4::after{content:"";display:block;width:60px;height:3px;background:var(--pink);margin-top:14px}
.foot ul li{list-style:none;font-size:13.5px;height:25.8px}
.ci{display:flex;gap:14px;font-size:12.5px;line-height:20px;align-items:flex-start}
.ci .round{width:24px;height:24px;flex:none}
</style>
</head>
<body>

<div class="abs topbar"><div class="pinkzone"></div></div>
<div class="abs call">
  <span class="round"><svg width="14" height="14" viewBox="0 0 24 24"><path fill="#fff" d="M6.6 10.8a15 15 0 0 0 6.6 6.6l2.2-2.2c.3-.3.7-.4 1-.2 1.1.4 2.3.6 3.6.6.6 0 1 .4 1 1V20c0 .6-.4 1-1 1A17 17 0 0 1 3 4c0-.6.4-1 1-1h3.5c.6 0 1 .4 1 1 0 1.3.2 2.5.6 3.6.1.3 0 .7-.2 1z"/></svg></span>
  <span><b>Call Us:</b> +1 555 0142 7700</span>
</div>
<div class="abs social-top" aria-label="Social links"><span></span><span></span><span></span></div>

<div class="abs logo" style="top:54px;left:116px;font-size:40px;line-height:38px">BRISK<small style="font-size:9px;margin-top:2px">THE ANSWER</small></div>
<nav class="abs nav">
  <span class="active" style="position:relative"><svg class="abs" style="top:-18px;left:10px" width="22" height="14" viewBox="0 0 22 14"><path d="M2 7l5 5L20 2" stroke="#e6177f" stroke-width="2.4" fill="none"/></svg>HOME</span>
  <span>PAYROLL</span><span>WHO WE ARE</span><span>CONTACT US</span>
</nav>
<div class="abs" style="top:76px;left:1021px;font-family:Montserrat,sans-serif;font-size:14px;color:var(--ink);display:flex;align-items:center;gap:8px">
  <svg width="16" height="16" viewBox="0 0 24 24" fill="none" stroke="#111" stroke-width="2"><circle cx="12" cy="12" r="10"/><path d="M2 12h20M12 2a15 15 0 0 1 0 20M12 2a15 15 0 0 0 0 20"/></svg>EN ▾
</div>

<div class="abs hero-photo" role="img" aria-label="Laptop on a desk showing a payroll dashboard"></div>
<svg class="abs" style="top:0;left:0" width="1200" height="820" viewBox="0 0 1200 820">
  <polygon points="0,581 229,745 1200,565 1200,820 0,820" fill="#fff"/>
  <polygon points="70,645 229,760 1056,608 229,776" fill="#e6177f"/>
</svg>
<h1 class="abs hero-title">YOUR TRUSTED<br>PAYROLLING PARTNER</h1>
<p class="abs hero-sub">Simplifying employment, empowering flexibility.</p>
<div class="abs hero-btn"><span class="btn">WHAT IS BRISK ? <svg class="tick" viewBox="0 0 22 14"><path d="M2 7l5 5L20 2" stroke="#e6177f" stroke-width="2.4" fill="none"/></svg></span></div>

<div class="abs center dots" style="top:828px"><i></i><i></i><i></i></div>
<h2 class="abs center heading" style="top:848px">WELCOME TO <b>BRISK</b></h2>
<p class="abs lead" style="top:910px;left:136px;width:928px;text-align:center">BRISK Your Stride is above all a story of men and women, a story of encounters and desire, a desire to share, a desire to refocus and a desire to breathe. Absorbed in a world that is running after time, it has become essential to find a little personal space to take precisely this time that we are running after until we run out of breath.Through our fiduciary activities at BRISK The Horizon and BRISK The Answer, we have been able to observe the growing imbalance in most of our lives and the desire was born to create this bubble of breathing space in a world that is constantly agitated.</p>
<div class="abs center" style="top:1072px"><span class="btn">WHAT IS BRISK ? <svg class="tick" viewBox="0 0 22 14"><path d="M2 7l5 5L20 2" stroke="#e6177f" stroke-width="2.4" fill="none"/></svg></span></div>

<div class="abs panel"></div>
<div class="abs center dots" style="top:1262px"><i></i><i></i><i></i></div>
<h2 class="abs center heading" style="top:1282px">OUR <b>SERVICES</b></h2>
<div class="abs service" style="left:170px">
  <div class="ring"><svg width="38" height="38" viewBox="0 0 24 24" fill="none" stroke="#e6177f" stroke-width="2"><rect x="3" y="8" width="18" height="12" rx="1"/><path d="M3 8l9 6 9-6M8 8V4h8v4"/></svg></div>
  <h3>PAYROLLING</h3><p>Lorem ipsum dolor sit amet, consectetur adipiscing elit, sed do eiusmod tempor incididunt</p>
</div>
<div class="abs divider" style="left:447px"></div>
<div class="abs service" style="left:480px">
  <div class="ring"><svg width="38" height="38" viewBox="0 0 24 24" fill="none" stroke="#e6177f" stroke-width="2"><circle cx="11" cy="11" r="8"/><path d="M3 11h16M11 3a12 12 0 0 1 0 16M11 3a12 12 0 0 0 0 16M17 17l5 5"/></svg></div>
  <h3>SOURCING</h3><p>Lorem ipsum dolor sit amet, consectetur adipiscing elit, sed do eiusmod tempor incididunt</p>
</div>
<div class="abs divider" style="left:756px"></div>
<div class="abs service" style="left:790px">
  <div class="ring"><svg width="38" height="38" viewBox="0 0 24 24" fill="none" stroke="#e6177f" stroke-width="2"><path d="M9 3h6l-2 4h-2zM12 7c-5 0-7 5-7 9a4 4 0 0 0 4 4h6a4 4 0 0 0 4-4c0-4-2-9-7-9z"/><path d="M12 10v7M10 12h3a1 1 0 0 1 0 2h-2a1 1 0 0 0 0 2h3"/></svg></div>
  <h3>PAYROLL OUTSOURCING</h3><p>Lorem ipsum dolor sit amet, consectetur adipiscing elit, sed do eiusmod tempor incididunt</p>
</div>
<div class="abs center" style="top:1586px"><span class="btn">VIEW MORE INFO <svg class="tick" viewBox="0 0 22 14"><path d="M2 7l5 5L20 2" stroke="#e6177f" stroke-width="2.4" fill="none"/></svg></span></div>

<div class="abs laptop-photo" role="img" aria-label="Laptop mockup showing a monthly payroll bar chart"></div>
<h2 class="abs heading" style="top:1810px;left:630px;font-size:31px">WHAT IS <b>PAYROLLING</b></h2>
<p class="abs" style="top:1860px;left:630px;width:450px;font-size:14.5px;line-height:23px;color:var(--ink)">Lorem ipsum dolor sit amet, consectetur adipiscing elit, sed do eiusmod tempor incididunt ut labore et dolore magna aliqua.</p>
<ul class="abs list" style="top:1916px;left:630px">
  <li><svg class="tick" viewBox="0 0 22 14"><path d="M2 7l5 5L20 2" stroke="#e6177f" stroke-width="2.4" fill="none"/></svg>Duis aute irure dolor in reprehenderit</li>
  <li><svg class="tick" viewBox="0 0 22 14"><path d="M2 7l5 5L20 2" stroke="#e6177f" stroke-width="2.4" fill="none"/></svg>Excepteur sint occaecat cupidatat non proident</li>
  <li><svg class="tick" viewBox="0 0 22 14"><path d="M2 7l5 5L20 2" stroke="#e6177f" stroke-width="2.4" fill="none"/></svg>Sed ut perspiciatis unde omnis iste natus</li>
  <li><svg class="tick" viewBox="0 0 22 14"><path d="M2 7l5 5L20 2" stroke="#e6177f" stroke-width="2.4" fill="none"/></svg>Nemo enim ipsam voluptatem quia voluptas</li>
</ul>

<div class="abs band"></div>
<h2 class="abs heading" style="top:2283px;left:113px;color:var(--white);font-size:31px">WHO <b>WE ARE</b></h2>
<p class="abs band-text" style="top:2336px">Lorem ipsum dolor sit amet, consectetur adipiscing elit, sed do eiusmod tempor incididunt ut labore et dolore magna aliqua. Ut enim ad minim veniam, quis nostrud exercitation ullamco laboris nisi ut aliquip ex ea commodo consequat.</p>
<p class="abs band-text" style="top:2464px">Duis aute irure dolor in reprehenderit in voluptate velit esse cillum dolore eu fugiat nulla pariatur. Excepteur sint occaecat cupidatat non proident, sunt in culpa qui officia deserunt mollit anim id est laborum.</p>
<div class="abs" style="top:2592px;left:113px"><span class="btn light" style="height:46px;font-size:14px">VIEW MORE INFO <svg class="tick" viewBox="0 0 22 14"><path d="M2 7l5 5L20 2" stroke="#e6177f" stroke-width="2.4" fill="none"/></svg></span></div>
<svg class="abs" style="top:2255px;left:680px" width="390" height="420" viewBox="0 0 390 420">
  <path d="M160 10a200 200 0 0 1 0 400a200 200 0 0 1-120-40a190 190 0 0 0 120 25a190 190 0 0 0 0-375a190 190 0 0 0-70 14a200 200 0 0 1 70-24z" fill="#fff"/>
</svg>
<div class="abs band-photo" role="img" aria-label="Hands typing on a laptop with floating payroll icons"></div>

<div class="abs center dots" style="top:2845px"><i></i><i></i><i></i></div>
<h2 class="abs center heading" style="top:2866px">JOIN THE <b>COMMUNITY</b></h2>
<p class="abs lead" style="top:2926px;left:158px;width:884px;text-align:center;font-size:15px;line-height:26.5px">Lorem ipsum dolor sit amet, consectetur adipiscing elit, sed do eiusmod tempor incididunt ut labore et dolore magna aliqua. Ut enim ad minim veniam, quis nostrud exercitation ullamco laboris nisi ut aliquip ex ea commodo consequat. Duis aute irure dolor in reprehenderit in voluptate velit esse cillum dolore eu fugiat nulla pariatur. Excepteur sint occaecat cupidatat non proident, sunt in culpa qui officia deserunt mollit anim id est laborum.</p>
<div class="abs center" style="top:3054px"><span class="btn">VIEW MORE INFO <svg class="tick" viewBox="0 0 22 14"><path d="M2 7l5 5L20 2" stroke="#e6177f" stroke-width="2.4" fill="none"/></svg></span></div>

<div class="abs testi-bg"></div>
<div class="abs center dots" style="top:3262px"><i></i><i></i><i></i></div>
<h2 class="abs center heading" style="top:3282px"><b>CLIENT</b> TESTIMONIALS</h2>
<div class="abs card" style="left:216px"><div class="stars">★★★★★</div><p>Excepteur sint occaecat cupidatat non proident, sunt in culpa qui officia deserunt mollit anim id est laborum.</p><div class="who"><b>MARA LINDT</b>Company Name</div></div>
<div class="abs avatar" style="left:146px" role="img" aria-label="Client portrait"></div>
<div class="abs card" style="left:694px"><div class="stars">★★★★★</div><p>Excepteur sint occaecat cupidatat non proident, sunt in culpa qui officia deserunt mollit anim id est laborum.</p><div class="who"><b>MARA LINDT</b>Company Name</div></div>
<div class="abs avatar" style="left:626px" role="img" aria-label="Client portrait"></div>
<svg class="abs" style="top:3448px;left:98px" width="16" height="28" viewBox="0 0 16 28"><path d="M14 2L3 14l11 12" stroke="#111" stroke-width="2" fill="none"/></svg>
<svg class="abs" style="top:3448px;left:1086px" width="16" height="28" viewBox="0 0 16 28"><path d="M2 2l11 12L2 26" stroke="#111" stroke-width="2" fill="none"/></svg>

<svg class="abs" style="top:3600px;left:0" width="1200" height="620" viewBox="0 0 1200 620">
  <rect x="0" y="0" width="1200" height="620" fill="#fff"/>
  <rect x="0" y="0" width="1200" height="146" fill="#f3f3f3"/>
  <polygon points="0,0 1200,0 1200,80 974,40 0,200" fill="#f3f3f3"/>
  <polygon points="0,239 974,75 1200,215 1200,620 0,620" fill="#111"/>
  <polygon points="147,195 970,30 1130,157 974,58" fill="#e6177f"/>
</svg>
<div class="abs logo" style="top:3925px;left:113px;font-size:66px;line-height:60px;color:#fff">BRISK<small style="font-size:14px;letter-spacing:17px;margin-top:4px">THE ANSWER</small></div>
<div class="abs" style="top:4037px;left:186px;display:flex;gap:10px" aria-label="Social links">
  <span style="width:28px;height:28px;border-radius:50%;background:#fff;display:block"></span>
  <span style="width:28px;height:28px;border-radius:50%;background:var(--pink);display:block"></span>
  <span style="width:28px;height:28px;border-radius:50%;background:#fff;display:block"></span>
</div>
<div class="abs foot" style="top:3886px;left:439px"><h4>QUICK LINKS</h4>
  <ul style="margin-top:16px;margin-left:6px"><li>Home</li><li>Who We Are</li><li>Services</li><li>FAQs</li><li>Contact</li></ul></div>
<div class="abs foot" style="top:3886px;left:602px"><h4>CONTACT US</h4>
  <div class="ci" style="margin-top:18px"><span class="round"><svg width="12" height="12" viewBox="0 0 24 24"><path fill="#fff" d="M6.6 10.8a15 15 0 0 0 6.6 6.6l2.2-2.2c.3-.3.7-.4 1-.2 1.1.4 2.3.6 3.6.6.6 0 1 .4 1 1V20c0 .6-.4 1-1 1A17 17 0 0 1 3 4c0-.6.4-1 1-1h3.5c.6 0 1 .4 1 1 0 1.3.2 2.5.6 3.6.1.3 0 .7-.2 1z"/></svg></span><span>+1 555 0142 7700</span></div>
  <div class="ci" style="margin-top:18px"><span class="round"><svg width="12" height="12" viewBox="0 0 24 24"><path fill="#fff" d="M2 5h20v14H2zM2 5l10 8 10-8" stroke="#e6177f" stroke-width="1.5"/></svg></span><span>hello@briskanswer.com</span></div>
  <div class="ci" style="margin-top:16px"><span class="round"><svg width="12" height="12" viewBox="0 0 24 24"><path fill="#fff" d="M12 2a7 7 0 0 0-7 7c0 5 7 13 7 13s7-8 7-13a7 7 0 0 0-7-7zm0 9.5a2.5 2.5 0 1 1 0-5 2.5 2.5 0 0 1 0 5z"/></svg></span><span>418 Harbor Lane #204<br>Easton, CA 90210</span></div>
</div>
<div class="abs foot" style="top:3886px;left:832px"><h4>SUBSCRIBE TO OUR BLOG</h4>
  <p style="margin-top:18px;margin-left:6px;font-size:12.5px;line-height:20px;width:250px">Sign up today to get resources on how to attract and retain more customers!</p>
  <div style="margin-top:16px;margin-left:6px;width:252px;height:34px;display:flex;border-radius:17px;overflow:hidden">
    <span style="flex:1;background:#fff;color:#888;font-size:11px;display:flex;align-items:center;padding-left:14px">✉ Email Address</span>
    <span style="width:48px;background:var(--pink);display:flex;align-items:center;justify-content:center"><svg width="16" height="16" viewBox="0 0 24 24"><path fill="#fff" d="M22 2L2 10l7 3 3 7z"/></svg></span>
  </div>
</div>
<div class="abs" style="top:4150px;left:113px;width:976px;height:1px;background:#555"></div>
<p class="abs center" style="top:4172px;color:#fff;font-size:13px">Copyrights@2025.Company Name.All Rights Reserved</p>

</body>
</html>
```